Pamphlet Days of the Family - École Val-Fleuri

We * need a pamphlet (flyer) to describe a new project. This project is called "Family Days - École Val-Fleuri". The text describing family days and their intended goals is attached in the downloaded .doc document. We also provided the logo (LE JOURNESS no font in attachment) which represents the school and those days of the family. Please write "Family Days - École Val-Fleuri" on top of the pamphlet with the Logo in plain view (The text The days of the École Val-Fleuri family must be associated with the logo). We need the pamphlet to be colorful, attractive and clean as much as possible. We would like to have childish drawings (see drawing example attached) and photos that represent one or both parents with their child (ren) in a SCHOOL ENVIRONMENT (very important). Parents must feel concerned. It can be a two-sided pamphlet. In color (bright colors as much as possible). The text must be in French so only FRENCH DESIGNERS ARE INVITED to work on this design because the text must remain consistent. The project can be summed up as follows: The Val-Fleuri School wishes to open its doors so that parents can share with their child moments in their student life. They will be invited, at various times of the school year, to participate in the daily life of their child, for example ... • during special activities in class (eg reading, do-it-yourself, job presentation, etc.). events (eg, back to school, Christmas choir, carnival, etc.) • during educational and sports outings (eg skating, library, cinema, etc.) Also, they will have the opportunity to come and spend a period in their child's classroom. They will have the privilege of accompanying him during a usual learning moment. For any additional question, thank you to contact me via this page, it will be my pleasure to answer you quickly. Thank you all for your participation. * We are a committee made up of parents, teachers, school principal, school administrators. Everyone has a say in the final design. So I am only the intermediary responsible for the project. It will be my pleasure to share with you the information received from these different partners for this project.

Target Market(s)

Parents of students at a primary school (ages 5 to 12).

Font styles to use
Sans Serif

Colors

Designer to choose colors to be used in the design.

Requirements
Must have
• The Logo prominently Pamphlet Colorful (beautiful bright colors) Easy to read and understand (some parents speak very little French) Originality (Attractive) Text In French (required) and consistent
Nice to have
• One or more Childish Drawing (s) One (1) parent-child Photo (s) in a school environment Allure Épuré
Should not have
• The Dark Colors Of the Scriptures Too Small A Condensed Text Text English

```html
<!DOCTYPE html>
<html lang="fr">
<head>
<meta charset="utf-8">
<title>Les journées de la famille de Val-Fleuri</title>
<link href="https://fonts.googleapis.com/css2?family=Raleway:wght@400;500;600;700&display=swap" rel="stylesheet">
<style>
  :root{
    --bg:#e4e6e8;
    --paper:#ffffff;
    --sun:#f2c21a;
    --orange:#f0915a;
    --green:#8fb43a;
    --blue-grey:#9aa9c9;
    --pink:#ef5a7a;
    --red:#e2243a;
    --sky:#2aa8df;
    --grass:#c3d82a;
    --ink:#4a3a2a;
    --text-grey:#555;
  }
  *{box-sizing:border-box;margin:0;padding:0}
  html,body{width:1200px;height:1200px;overflow:hidden}
  body{background:var(--bg);font-family:"Raleway",sans-serif;color:var(--ink);position:relative}

  /* inside spread */
  .spread{position:absolute;left:40px;top:30px;width:1120px;height:530px;background:var(--paper);box-shadow:0 6px 18px rgba(0,0,0,.15)}
  .spread-field{position:absolute;inset:18px;border-radius:26px;overflow:hidden;
    background:linear-gradient(100deg,var(--sun) 0%,#f6cf4c 30%,#fbe6a8 55%,#fdf3d9 75%,#fff8ea 100%)}
  .fold{position:absolute;left:560px;top:0;bottom:0;width:1px;background:rgba(0,0,0,.08)}
  .abs{position:absolute}
  .intro{left:22px;top:22px;width:350px;font-size:11.5px;line-height:1.35;font-weight:600}
  .intro ul{margin:4px 0 4px 16px;font-weight:500}
  .intro p.more{font-weight:500}
  .bubble{position:absolute;border-radius:50%;display:flex;flex-direction:column;align-items:center;justify-content:center;text-align:center;padding:12px 26px;color:#3d2a20}
  .bubble h3{font-weight:500;font-size:18px;margin-bottom:6px}
  .bubble p{font-size:11.5px;font-weight:600;line-height:1.25;margin-bottom:5px}
  .b-child{left:380px;top:12px;width:270px;height:180px;background:rgba(240,135,80,.85)}
  .b-school{left:130px;top:258px;width:300px;height:136px;background:rgba(130,170,50,.9)}
  .b-teacher{left:240px;top:392px;width:310px;height:100px;background:rgba(240,140,40,.85)}
  .b-teacher h3{font-size:16px;margin-bottom:4px}
  .b-teacher p{font-size:11px;margin-bottom:3px}
  .b-parent{left:790px;top:230px;width:290px;height:165px;background:rgba(150,165,205,.9)}
  .pill{position:absolute;border-radius:50%;background:var(--pink);color:#fff;font-size:11px;display:flex;align-items:center;justify-content:center;text-align:center;line-height:1.1}
  .pill-child{left:480px;top:192px;width:100px;height:46px}
  .pill-parent{left:720px;top:278px;width:100px;height:52px}
  .pill-school{left:430px;top:336px;width:116px;height:50px;background:#ef6a3a}
  .links{position:absolute;inset:0;pointer-events:none}
  .center-title{left:470px;top:248px;width:210px;color:var(--red);font-weight:700;font-size:19px;line-height:1.05;transform:rotate(-12deg)}
  .photo{left:660px;top:0;width:440px;height:222px;border-radius:0 26px 26px 26px;
    background:linear-gradient(135deg,#f1efe9 0%,#c7b9a6 40%,#9a4a4a 62%,#3d5ea6 100%)}
  .drawing{position:absolute;border-radius:40px;opacity:.85}
  .d-boy{left:20px;top:390px;width:110px;height:120px;background:linear-gradient(180deg,#f7efe0,#9ccc5a 55%,#7a5aa8)}
  .d-girl{left:560px;top:405px;width:130px;height:95px;background:linear-gradient(180deg,#fbe9c8,#f4d640 70%,#e24a3a)}
  .d-mum{left:870px;top:390px;width:120px;height:110px;background:linear-gradient(180deg,#f09a55,#e03a2a)}

  /* back cover */
  .back{position:absolute;left:40px;top:595px;width:540px;height:575px;background:var(--paper);box-shadow:0 6px 18px rgba(0,0,0,.15);text-align:center}
  .brand-name{position:absolute;left:0;right:0;top:250px;color:var(--ink);font-weight:600;font-size:26px}
  .back-note{position:absolute;left:50px;right:50px;top:430px;font-size:14px;line-height:1.4;color:var(--text-grey)}
  .back-note small{display:block;margin-top:12px;font-size:11px}

  /* front cover */
  .front{position:absolute;left:620px;top:595px;width:540px;height:575px;background:var(--paper);box-shadow:0 6px 18px rgba(0,0,0,.15)}
  .front-panel{position:absolute;inset:20px;border-radius:24px;overflow:hidden;background:linear-gradient(180deg,var(--sky) 0%,#7cc6ea 30%,#e6f3fa 58%,#fff 62%)}
  .front-title{position:absolute;left:0;right:0;top:28px;text-align:center;color:#f3e03a;font-size:44px;font-weight:400;line-height:1}
  .front-title span{display:block;color:#fff;font-size:24px;margin-top:6px}
  .front-drawing{position:absolute;left:30px;right:30px;top:170px;height:190px;border-radius:20px;
    background:linear-gradient(180deg,rgba(255,255,255,0) 0%,rgba(240,120,90,.35) 45%,rgba(120,190,90,.45) 100%)}
  .front-band{position:absolute;left:0;right:0;bottom:0;height:170px;background:var(--grass);color:#fff;font-size:14.5px;line-height:1.5;padding:22px 28px;font-weight:500}
  .front-band strong{color:#2a8ac8;font-weight:600}
</style>
</head>
<body>

<section class="spread" aria-label="Intérieur du dépliant">
  <div class="spread-field">
    <div class="fold"></div>

    <div class="abs intro">
      <p>Vous serez invités, à divers moments de l’année scolaire, à participer au quotidien de votre enfant, par exemple…</p>
      <ul>
        <li>lors d’activités spéciales en classe (ex : lecture, bricolage, présentation de métiers, etc.)</li>
        <li>lors d’événements (ex : la rentrée, chorale de Noël, fête foraine, etc.)</li>
        <li>lors de sorties éducatives et sportives (ex : patinage, bibliothèque, cinéma, etc.)</li>
      </ul>
      <p class="more">De plus, vous aurez l’opportunité de venir passer une période dans la classe de votre enfant. Vous aurez ainsi le privilège de l’accompagner lors d’un moment d’apprentissage habituel.</p>
    </div>

    <div class="abs photo" role="img" aria-label="Photo : des parents avec leurs enfants dans un couloir d’école"></div>

    <div class="bubble b-child">
      <h3>Pour l’enfant :</h3>
      <p>Être fier de partager un moment de sa vie scolaire, en toute simplicité, avec son parent.</p>
      <p>Développer son plein potentiel.</p>
      <p>Favoriser sa réussite éducative.</p>
    </div>
    <div class="bubble b-school">
      <h3>Pour l’école :</h3>
      <p>Vivre un projet rassembleur.</p>
      <p>Valoriser le travail de l’équipe-école.</p>
      <p>Rayonner dans sa communauté.</p>
    </div>
    <div class="bubble b-teacher">
      <h3>Pour l’enseignant :</h3>
      <p>Encourager la réussite de ses élèves.</p>
      <p>Multiplier les moments privilégiés parent-enfant-enseignant dans le milieu scolaire.</p>
    </div>
    <div class="bubble b-parent">
      <h3>Pour le parent</h3>
      <p>Développer un sentiment d’appartenance envers l’école.</p>
      <p>Découvrir son enfant en tant qu’élève.</p>
      <p>Participer à la réussite et à la persévérance scolaire de son enfant.</p>
    </div>

    <svg class="links" width="1084" height="494" viewBox="0 0 1084 494" aria-hidden="true">
      <g stroke="#fff" stroke-width="3" fill="none" stroke-linecap="round">
        <path d="M560 215 Q650 225 740 290"/>
        <path d="M740 320 Q640 350 546 360"/>
        <path d="M482 338 Q495 290 510 238"/>
      </g>
    </svg>

    <div class="pill pill-child">Enfant</div>
    <div class="pill pill-parent">Parent</div>
    <div class="pill pill-school">École<br>Enseignant(e)s</div>

    <div class="abs center-title">Les journées<br>de la famille<br>de Val-Fleuri</div>

    <div class="drawing d-boy" role="img" aria-label="Dessin d’enfant : un garçon souriant"></div>
    <div class="drawing d-girl" role="img" aria-label="Dessin d’enfant : une fillette tenant une fleur"></div>
    <div class="drawing d-mum" role="img" aria-label="Dessin d’enfant : une maman aux cheveux roux"></div>
  </div>
</section>

<section class="back" aria-label="Verso du dépliant">
  <p class="brand-name">Journées Val-Fleuri</p>
  <p class="back-note">Pour chaque occasion reliée au projet « Les journées de la famille de Val-Fleuri », vous serez informés par l’enseignant(e) de votre enfant afin que vous puissiez y participer.
    <small>Surveillez les apparitions du nom sur les communications lors des Journées de la famille de Val-Fleuri !</small>
  </p>
</section>

<section class="front" aria-label="Couverture du dépliant">
  <div class="front-panel">
    <h1 class="front-title">Les journées<br>de la famille<span>de Val-Fleuri</span></h1>
    <div class="front-drawing" role="img" aria-label="Dessin d’enfant : une famille se tenant la main devant une maison, sous le soleil"></div>
    <div class="front-band">
      <strong>L’école Val-Fleuri</strong> souhaite ouvrir ses portes afin que vous puissiez partager avec votre enfant des moments de sa vie d’élève. Vous connaissez votre enfant sous plusieurs de ses facettes. Avec ce projet, vous pourrez maintenant le connaître en tant qu’élève œuvrant dans son milieu scolaire.
    </div>
  </div>
</section>

</body>
</html>
```